I am a general contractor in Portland, Or. I would like a clean and simple design layout, maybe using the "didot" font, blue and dark bronze in colors are preferred. On one side of the card, it would be nice to have a logo(attached photo) and business name(KTW Construction). I don't need my job title on the card, just some thing along the lines of "gordon pike, general contractor". Thanks much.

Target Market(s)

Adults from 30-55 years old. Middle to upper class.

Industry/Entity Type

Contractor

Contact Information for Business Card

KTW Construction
Gordon L. Pike
2843 NE 71st Ave.
Portland, Or. 97288
541.555.0187

Font styles to use
Other font styles liked:
• didot

Colors
3277b5
7f7f7f

Requirements
Should not have
• Too much going on.

```html
<!DOCTYPE html>
<html lang="en">
<head>
<meta charset="utf-8">
<title>KTW Construction — Business Card</title>
<link rel="stylesheet" href="https://fonts.googleapis.com/css2?family=Exo+2:wght@600;700&family=Michroma&display=swap">
<style>
  :root {
    --backdrop: #e4e5e6;
    --card: #ffffff;
    --navy: #2b3a8f;
    --sky: #3a9be0;
    --charcoal: #3b3c3e;
    --accent-red: #e2393f;
    --ink: #4a4a4f;
    --rule: #9a9a9f;
  }
  * { box-sizing: border-box; margin: 0; padding: 0; }
  html, body { width: 1200px; height: 771px; overflow: hidden; }
  body {
    background: var(--backdrop);
    display: flex;
    align-items: center;
    justify-content: center;
    gap: 40px;
  }
  .card {
    position: relative;
    width: 540px;
    height: 309px;
    background: var(--card);
    box-shadow: 0 6px 18px rgba(0,0,0,0.15);
    overflow: hidden;
  }
  .card__swoosh { position: absolute; inset: 0; width: 100%; height: 100%; }

  .brand {
    position: absolute;
    display: flex;
    flex-direction: column;
    align-items: center;
    gap: 8px;
  }
  .brand__dot {
    width: 46px; height: 46px;
    border-radius: 50%;
    background: var(--sky);
  }
  .brand__name {
    font-family: "Exo 2", sans-serif;
    font-weight: 700;
    color: var(--navy);
    line-height: 1.05;
    text-align: center;
  }
  .card--front .brand { top: 24px; right: 58px; }
  .card--front .brand__name { font-size: 27px; }

  .card--back .brand { inset: 0; justify-content: center; gap: 16px; }
  .card--back .brand__dot { width: 110px; height: 110px; }
  .card--back .brand__name { font-size: 30px; }

  .details {
    position: absolute;
    top: 140px;
    left: 200px;
    display: flex;
    gap: 14px;
    font-family: "Michroma", sans-serif;
    font-size: 8.5px;
    color: var(--ink);
    letter-spacing: 0.04em;
    line-height: 1.75;
  }
  .details__person { text-align: right; }
  .details__name { color: var(--accent-red); font-size: 10px; }
  .details__divider { width: 1px; background: var(--rule); }
  .contact-list { list-style: none; padding-top: 2px; }
  .contact-list li { display: flex; align-items: center; gap: 6px; }
  .contact-list svg { width: 10px; height: 10px; flex: none; }
</style>
</head>
<body>

  <section class="card card--front" aria-label="Front of card">
    <svg class="card__swoosh" viewBox="0 0 540 309" preserveAspectRatio="none" aria-hidden="true">
      <defs>
        <linearGradient id="swooshTone" x1="0" y1="0" x2="1" y2="0">
          <stop offset="0" stop-color="#3b3c3e"/>
          <stop offset="0.45" stop-color="#2f2f36"/>
          <stop offset="1" stop-color="#2b3a8f"/>
        </linearGradient>
      </defs>
      <path d="M0 110 C120 232 330 290 540 292 L540 309 L0 309 Z" fill="url(#swooshTone)"/>
      <path d="M0 96 C130 222 330 282 540 284" fill="none" stroke="#8c8c92" stroke-width="2"/>
      <path d="M200 262 C320 298 440 300 540 298" fill="none" stroke="#ffffff" stroke-width="1.5" opacity="0.7"/>
    </svg>

    <div class="brand">
      <span class="brand__dot"></span>
      <span class="brand__name">KTW<br>Construction</span>
    </div>

    <div class="details">
      <div class="details__person">
        <p class="details__name">Gordon Pike</p>
        <p>General Contractor</p>
        <p>2843 NE 71st Ave.</p>
        <p>Portland, Or. 97288</p>
      </div>
      <span class="details__divider"></span>
      <ul class="contact-list">
        <li><svg viewBox="0 0 10 10" aria-hidden="true"><circle cx="5" cy="5" r="5" fill="#e2393f"/><path d="M3.3 2.6c.4 1.9 1.6 3.3 3.3 4.5" stroke="#fff" stroke-width="1.2" fill="none" stroke-linecap="round"/></svg>541.555.0187</li>
      </ul>
    </div>
  </section>

  <section class="card card--back" aria-label="Back of card">
    <div class="brand">
      <span class="brand__dot"></span>
      <span class="brand__name">KTW Construction</span>
    </div>
  </section>

</body>
</html>
```